Belmont Ridge Business Card Design Project

We have recently rebranded and would like to design new business cards that incorporate the corporate logo - double sided cards with corporate logo on one side and contact details on the other

Target Market(s)

Sophisticated and high net worth investors and finance industry professionals

Industry/Entity Type

Funds Management

Contact Information for Business Card

The card should prominently feature the company name and logo. Other details will be standard contact details for each staff member - name, address, phone, email, website

Colors
0054AA
0677BA
7BADD7
CADEEF
E8F1F8

Requirements
Must have
• Double-sided design with one side prominently featuring the corporate logo and the other side with all standard contact details

```html
<!DOCTYPE html>
<html lang="en">
<head>
<meta charset="utf-8">
<title>Belmont Ridge Business Cards</title>
<link rel="stylesheet" href="https://fonts.googleapis.com/css2?family=Cinzel:wght@400&family=Arimo:wght@400;700&display=swap">
<style>
  :root {
    --page-bg: #e9e9e9;
    --card-navy: #1f4475;
    --card-deep: #102c56;
    --card-mid: #2a5a94;
    --card-light: #4a86c8;
    --ink-white: #ffffff;
    --ink-soft: rgba(255,255,255,0.75);
  }
  * { margin: 0; padding: 0; box-sizing: border-box; }
  html, body { width: 1200px; height: 802px; overflow: hidden; }
  body {
    background: var(--page-bg);
    position: relative;
    font-family: "Arimo", Arial, sans-serif;
  }
  .card {
    position: absolute;
    top: 241px;
    width: 560px;
    height: 320px;
    background: var(--card-navy);
    color: var(--ink-white);
    overflow: hidden;
    box-shadow: 0 6px 16px rgba(0,0,0,0.18);
  }
  .card--contact { left: 30px; }
  .card--brand { left: 610px; }

  .contact-wordmark {
    position: absolute;
    left: 40px;
    top: 146px;
    width: 220px;
    text-align: center;
    font-family: "Cinzel", Georgia, serif;
    font-size: 25px;
    letter-spacing: 0.5px;
    color: var(--ink-white);
  }
  .contact-divider {
    position: absolute;
    left: 290px;
    top: 62px;
    width: 1px;
    height: 196px;
    background: var(--ink-soft);
  }
  .contact-details {
    position: absolute;
    left: 312px;
    top: 66px;
  }
  .contact-name {
    font-weight: 700;
    font-size: 18px;
    letter-spacing: 0.5px;
    text-transform: uppercase;
  }
  .contact-role { font-size: 13px; margin-top: 3px; }
  .contact-address { font-size: 13px; line-height: 17px; margin-top: 14px; }
  .contact-list { list-style: none; margin-top: 12px; font-size: 13px; }
  .contact-list li { display: flex; align-items: center; gap: 8px; height: 19px; }
  .contact-list svg { width: 12px; height: 12px; flex: none; }

  .brand-wordmark {
    position: absolute;
    right: 36px;
    top: 48px;
    font-family: "Cinzel", Georgia, serif;
    font-size: 40px;
    color: #e8eef6;
    letter-spacing: 1px;
  }
  .brand-motif {
    position: absolute;
    left: 0;
    top: 150px;
    width: 420px;
    height: 170px;
    background: linear-gradient(100deg, var(--card-deep) 0%, var(--card-mid) 55%, var(--card-light) 100%);
    opacity: 0.9;
  }
</style>
</head>
<body>
  <section class="card card--contact">
    <div class="contact-wordmark">Belmont Ridge</div>
    <div class="contact-divider"></div>
    <div class="contact-details">
      <div class="contact-name">Daniel Hartley</div>
      <div class="contact-role">Manager</div>
      <div class="contact-address">Your Address, City<br>State, Zip 0000</div>
      <ul class="contact-list">
        <li>
          <svg viewBox="0 0 12 12" aria-hidden="true"><circle cx="6" cy="6" r="6" fill="#fff"/><path d="M3.8 3.2l1.2 0 .5 1.5-.8.6a4 4 0 0 0 1.9 1.9l.6-.8 1.5.5v1.2c0 .4-.4.7-.8.6A5.4 5.4 0 0 1 3.2 4c0-.4.2-.8.6-.8z" fill="#1f4475"/></svg>
          555-014-2100
        </li>
        <li>
          <svg viewBox="0 0 12 12" aria-hidden="true"><rect x="0.5" y="2.5" width="11" height="7" fill="#fff"/><path d="M0.8 2.8L6 6.6l5.2-3.8" fill="none" stroke="#1f4475" stroke-width="1"/></svg>
          daniel@belmontridge.com
        </li>
        <li>
          <svg viewBox="0 0 12 12" aria-hidden="true"><circle cx="6" cy="6" r="6" fill="#fff"/><ellipse cx="6" cy="6" rx="2.2" ry="5" fill="none" stroke="#1f4475" stroke-width="0.9"/><path d="M1 6h10" stroke="#1f4475" stroke-width="0.9"/></svg>
          www.belmontridge.com
        </li>
      </ul>
    </div>
  </section>

  <section class="card card--brand">
    <div class="brand-wordmark">Belmont Ridge</div>
    <div class="brand-motif" role="img" aria-label="Large decorative brand motif in layered blue tones"></div>
  </section>
</body>
</html>
```